New Webpage for High Class Expert Witness Services Company

We are looking for a minimalist design for a webpage that just has our logo and an entry form offer to connect with one of our Liaisons.
The entry form should just ask for Name, Email, Contact Info and Description of Project.

Company Name is: The Marlowe Crest Advisory Services

Number of Pages Required

1 page

```html
<!DOCTYPE html>
<html lang="en">
<head>
<meta charset="utf-8">
<title>Marlowe Crest Advisory Services — Connect With A Liaison</title>
<link rel="stylesheet" href="https://fonts.googleapis.com/css2?family=Cinzel:wght@500;600&family=Poppins:wght@400;500;600&display=swap">
<style>
  :root {
    --page-bg: #000000;
    --card-bg: #000000;
    --card-border: #2a2a2a;
    --field-bg: #0d0d0d;
    --field-border: #2e2e2e;
    --text-main: #ffffff;
    --text-soft: #e6e6e6;
    --text-placeholder: #8a8a8a;
    --icon: #8c8c8c;
    --rule: #3a3a3a;
    --silver-a: #bdbec2;
    --silver-b: #e2e3e5;
    --button-text: #111111;
  }
  * { box-sizing: border-box; margin: 0; padding: 0; }
  html, body { width: 1200px; height: 1007px; overflow: hidden; background: var(--page-bg); }
  body { position: relative; font-family: 'Poppins', sans-serif; color: var(--text-main); }

  .hero-photo {
    position: absolute; left: 0; top: 0; width: 1200px; height: 185px;
    background: linear-gradient(90deg, #2b2b2b 0%, #4a4a4a 22%, #2a2a2a 45%, #3d3d3d 70%, #262626 100%);
    border-bottom: 1px solid #3a3a3a;
  }
  .hero-photo::after {
    content: ""; position: absolute; inset: 0;
    background: linear-gradient(180deg, rgba(0,0,0,0.25), rgba(0,0,0,0.45));
  }
  .brand {
    position: absolute; top: 68px; left: 0; width: 1200px;
    display: flex; justify-content: center; align-items: center; gap: 12px; z-index: 2;
  }
  .brand-mark { width: 14px; height: 14px; background: var(--text-soft); }
  .brand-name {
    font-family: 'Cinzel', serif; font-weight: 600; font-size: 27px;
    letter-spacing: 1px; color: var(--text-soft);
  }

  .backdrop {
    position: absolute; left: 0; top: 186px; width: 1200px; height: 821px;
    background:
      radial-gradient(ellipse 420px 260px at 60px 560px, rgba(120,120,120,0.35), transparent 70%),
      radial-gradient(ellipse 520px 200px at 900px 640px, rgba(70,70,70,0.35), transparent 70%),
      #000;
  }

  .liaison-card {
    position: absolute; left: 297px; top: 235px; width: 606px; height: 676px;
    background: var(--card-bg); border: 1px solid var(--card-border); border-radius: 22px;
  }
  .card-title {
    position: absolute; top: 272px; left: 0; width: 1200px; text-align: center;
    font-family: 'Cinzel', serif; font-weight: 600; font-size: 31px; letter-spacing: 0.5px;
  }
  .card-intro {
    position: absolute; top: 315px; left: 0; width: 1200px; text-align: center;
    font-size: 13px; line-height: 20px; color: var(--text-soft);
  }
  .card-divider { position: absolute; top: 370px; left: 445px; width: 314px; height: 24px; }

  .form-label { position: absolute; left: 356px; font-size: 12.5px; color: var(--text-soft); }
  .form-field {
    position: absolute; left: 356px; width: 487px; height: 46px;
    background: var(--field-bg); border: 1px solid var(--field-border); border-radius: 6px;
    display: flex; align-items: center; padding-left: 12px; gap: 10px;
    font-size: 12px; color: var(--text-placeholder);
  }
  .form-field.is-textarea { height: 108px; align-items: flex-start; padding-top: 14px; }
  .form-field svg { flex: none; width: 16px; height: 16px; stroke: var(--icon); fill: none; stroke-width: 1.3; }

  .submit-button {
    position: absolute; left: 356px; top: 822px; width: 487px; height: 53px; border-radius: 6px;
    background: linear-gradient(90deg, var(--silver-a), var(--silver-b));
    display: flex; justify-content: center; align-items: center;
    font-weight: 600; font-size: 12.5px; color: var(--button-text); letter-spacing: 0.3px;
  }

  .footer-rule { position: absolute; left: 136px; top: 944px; width: 918px; height: 1px; background: var(--rule); }
  .footer-note { position: absolute; top: 969px; left: 0; width: 1200px; text-align: center; font-size: 13px; color: var(--text-soft); }
</style>
</head>
<body>
  <div class="hero-photo" role="img" aria-label="Greyscale photo of medical experts working in a laboratory"></div>
  <div class="brand">
    <span class="brand-mark"></span>
    <span class="brand-name">MARLOWE CREST ADVISORY SERVICES</span>
  </div>

  <div class="backdrop" role="img" aria-label="Dark background with soft flowing grey light waves"></div>

  <div class="liaison-card"></div>
  <h1 class="card-title">CONNECT WITH A LIAISON</h1>
  <p class="card-intro">High-Class Expert Witness Support. Share Your Project Details And A<br>Dedicated Liaison Will Reach You Within 24 Hours.</p>
  <svg class="card-divider" viewBox="0 0 314 24">
    <line x1="0" y1="12" x2="135" y2="12" stroke="#3a3a3a" stroke-width="1"/>
    <line x1="179" y1="12" x2="314" y2="12" stroke="#3a3a3a" stroke-width="1"/>
    <circle cx="157" cy="12" r="6" fill="#cfcfcf"/>
  </svg>

  <label class="form-label" style="top:416px">Full Name *</label>
  <div class="form-field" style="top:440px">
    <svg viewBox="0 0 16 16"><circle cx="8" cy="5" r="3"/><path d="M2.5 15c0-3.2 2.5-5 5.5-5s5.5 1.8 5.5 5"/></svg>
    First Name
  </div>

  <label class="form-label" style="top:500px">Email Address *</label>
  <div class="form-field" style="top:525px">
    <svg viewBox="0 0 16 16"><path d="M1.5 6.5 8 2l6.5 4.5V14h-13z"/><path d="M1.5 6.5 8 10.5l6.5-4"/></svg>
    Your Email
  </div>

  <label class="form-label" style="top:585px;left:358px">Contact Info (Phone / Direct Line) *</label>
  <div class="form-field" style="top:609px">
    <svg viewBox="0 0 16 16"><path d="M3 1.5h3l1 3.5-2 1.2a8 8 0 0 0 4.8 4.8L11 9l3.5 1v3a1.5 1.5 0 0 1-1.6 1.5A12 12 0 0 1 1.5 3.1 1.5 1.5 0 0 1 3 1.5z"/><path d="M11 2v3M13.5 2v3"/></svg>
    Phone
  </div>

  <label class="form-label" style="top:670px">Description Of Project *</label>
  <div class="form-field is-textarea" style="top:695px">
    <svg viewBox="0 0 16 16"><path d="M8 2c3.6 0 6.5 2.4 6.5 5.5S11.6 13 8 13c-.9 0-1.7-.1-2.4-.4L2 14l1-3A5.2 5.2 0 0 1 1.5 7.5C1.5 4.4 4.4 2 8 2z"/><path d="M5 6.5h6M5 9h4"/></svg>
    Provide Key Case Details, Litigation Area, Required Expertise, Deadlines...
  </div>

  <div class="submit-button">SUBMIT NOW</div>

  <div class="footer-rule"></div>
  <p class="footer-note">2026 The Marlowe Crest Advisory Services All Right</p>
</body>
</html>
```